Professional Website for Leading Global Private Equity Real Estate Company

The company is a leading global Private Equity Real Estate (Altavera). We need a homepage design, an inner page design, and color/font tweaks to the logo (color should be more soothing than current blue used in the logo). The logo website should project the company as global, professional, experienced, trustworthy, accessible, YOUNG, DYNAMIC, hi-tech. PLEASE SEE the attached Design Brief Word Doc for details.

Target Market(s)

institional investors and wealthy private individuals

Industry/Entity Type

Finance

Number of Pages Required

2 page

Font styles to use
Sans Serif
Other font styles liked:
• either like in https://www.ferndalequay.com/ or like in presentations (Montserrat Black & Montserrat Light, Century Gothic, Blair ITC, Almoni Neue DL 4.0 AAA Medium, Almoni DL AAA)

Requirements
Must have
• new color palette that is NOT based on current logo. they want a more soothing color palette than the blue in that logo. the new color palette should project: global, professional, experienced, trustworthy, accessible, YOUNG, DYNAMIC, hi-tech.
Nice to have
• the likes these sites: https://www.ferndalequay.com/ and https://www.tvr.law/

```html
<!DOCTYPE html>
<html lang="en">
<head>
<meta charset="utf-8">
<title>Altavera Real Estate</title>
<link rel="stylesheet" href="https://fonts.googleapis.com/css2?family=Montserrat:wght@300;400;500;600;700;800&display=swap">
<style>
:root{
  --blue:#1ea5e6;
  --cyan:#3fc3f5;
  --deep:#1273a8;
  --navy:#0d5782;
  --ink:#111;
  --text:#333;
  --black:#050505;
  --white:#fff;
}
*{margin:0;padding:0;box-sizing:border-box}
html,body{width:1200px;height:4570px;overflow:hidden}
body{font-family:"Montserrat",sans-serif;color:var(--text);background:var(--white);position:relative}
section,header,footer{position:absolute;left:0;width:1200px}
.abs{position:absolute}
.center{text-align:center;left:0;width:1200px}
h2{font-weight:700;font-size:29px;color:var(--ink);letter-spacing:.5px}
.underline::after{content:"";display:block;width:78px;height:3px;background:var(--blue);margin:6px auto 0}
.underline.left::after{margin-left:0}
.lead{font-size:15px;line-height:26px;color:#333}
.btn{position:absolute;background:var(--cyan);color:var(--white);font-weight:700;font-size:15px;letter-spacing:.8px;display:flex;align-items:center;justify-content:center;text-transform:uppercase}

/* hero */
.hero{top:0;height:685px;background:linear-gradient(180deg,#1c2533 0%,#2e3a48 35%,#4b4f44 70%,#2d3a2a 100%)}
.brand{display:flex;align-items:center;gap:10px;font-weight:500;font-size:19px;letter-spacing:2px;color:var(--cyan)}
.brand .dot{width:22px;height:22px;border-radius:50%;background:var(--cyan)}
.nav{top:47px;left:470px;display:flex;gap:24px;font-size:14px;color:#e8e8e8}
.nav .active{color:var(--cyan);font-weight:600}
.hero-title{top:210px;color:var(--white);text-align:center}
.hero-title .small{font-size:42px;font-weight:300;letter-spacing:1px}
.hero-title .big{font-size:48px;font-weight:800;letter-spacing:1px;margin-top:4px}
.hero-point{top:385px;width:412px;border-top:2px solid var(--white);padding-top:22px;color:var(--white);font-size:15px;line-height:26px;font-weight:500}

/* about counters */
.counter{position:absolute;width:184px;height:186px;color:var(--white);text-align:center;font-weight:700;font-size:28px;line-height:42px;padding-top:52px;background:var(--c)}
.counter::before{content:"";position:absolute;inset:-7px -7px -7px -7px;border:3px solid var(--c);pointer-events:none}
.counter .num{font-size:32px}
.tag{position:absolute;width:86px;border-bottom:2px solid var(--blue);border-top:2px solid var(--blue);text-align:center;font-weight:600;font-size:16px;color:var(--ink);padding:3px 0}

/* platforms */
.platforms{top:1415px;height:632px;background:linear-gradient(135deg,#dfeaf2,#eef4f8 45%,#d3e2ec)}
.card{position:absolute;top:1624px;width:200px;height:306px;text-align:center}
.card .photo{height:180px;background:linear-gradient(135deg,#8d9aa5,#d7dde2)}
.card h3{font-size:17px;font-weight:700;color:var(--ink);margin-top:17px}
.card p{font-size:12.5px;line-height:20px;color:#333;margin-top:6px}
.card .more{font-size:14px;font-weight:700;color:var(--blue);margin-top:6px}
.card.featured{background:var(--white);box-shadow:0 4px 14px rgba(0,0,0,.25)}

.body-copy{font-size:15px;line-height:25.7px;text-align:justify;color:#333}
.round-photo{position:absolute;width:380px;height:380px;border-radius:50%}

/* stay updated */
.stay{top:2604px;height:304px;background:linear-gradient(120deg,#2aa5e8,#46c4f7 60%,#2aa8e8)}
.stay h2,.stay .lead{color:var(--white)}
.field{position:absolute;top:2789px;height:44px;display:flex;align-items:center;font-weight:700;font-size:15px}

/* contact */
.touch{top:3465px;height:698px;background:linear-gradient(135deg,#eef3f6,#f8fafb 50%,#e4edf2)}
.info{display:flex;align-items:center;gap:14px;font-size:14px;line-height:22px;color:#111}
.ico{width:30px;height:30px;border-radius:50%;background:var(--blue);flex:none;display:flex;align-items:center;justify-content:center}
.form-field{position:absolute;border-bottom:1px solid #9aa;padding-bottom:10px}
.form-field label{display:block;font-weight:700;font-size:16px;color:#111}
.form-field span{font-size:13.5px;color:#333}

/* footer */
.footer{top:4163px;height:407px;background:var(--black);color:var(--white)}
.footer h4{font-weight:700;font-size:19px;letter-spacing:.5px}
.links{list-style:none;font-size:14.5px;line-height:32px}
.links li::before{content:"» ";}
.foot-info{display:flex;gap:14px;font-size:14px;line-height:22px;align-items:flex-start}
.social{display:flex;gap:16px}
.social span{width:26px;height:26px;border-radius:50%;background:var(--blue)}
</style>
</head>
<body>

<header class="hero">
  <div class="abs brand" style="top:44px;left:108px"><span class="dot"></span>ALTAVERA REAL ESTATE</div>
  <nav class="abs nav">
    <span class="active">Home</span><span>About Us</span><span>Our Businesses ▾</span><span>Investors Lobby ▾</span><span>News ▾</span><span>Contact Us</span>
    <svg width="16" height="16" viewBox="0 0 16 16"><circle cx="6.5" cy="6.5" r="5" fill="none" stroke="#fff" stroke-width="2"/><line x1="10" y1="10" x2="15" y2="15" stroke="#fff" stroke-width="2.4"/></svg>
  </nav>
  <div role="img" aria-label="Photo of a large two-storey family house at dusk" class="abs" style="top:0;left:260px;width:680px;height:685px;background:radial-gradient(ellipse at 50% 45%,rgba(200,180,150,.35),rgba(0,0,0,0) 60%)"></div>
  <div class="abs hero-title center">
    <div class="small">WELCOME TO</div>
    <div class="big">ALTAVERA REAL ESTATE</div>
  </div>
  <div class="abs hero-point" style="left:112px">
    Lorem ipsum dolor sit amet, consectetur<br>adipiscing elit, 2003
    <svg class="abs" style="right:24px;top:30px" width="32" height="16" viewBox="0 0 32 16"><path d="M0 8h28M21 2l7 6-7 6" stroke="#fff" stroke-width="3" fill="none"/></svg>
  </div>
  <div class="abs hero-point" style="left:675px">
    Lorem ipsum dolor sit amet, consectetur<br>adipiscing elit, 2003
    <svg class="abs" style="right:24px;top:30px" width="32" height="16" viewBox="0 0 32 16"><path d="M0 8h28M21 2l7 6-7 6" stroke="#fff" stroke-width="3" fill="none"/></svg>
  </div>
  <div class="btn" style="top:525px;left:520px;width:144px;height:43px">About Us</div>
</header>

<section class="about" style="top:685px;height:730px">
  <h2 class="abs center underline" style="top:80px">ABOUT US</h2>
  <p class="abs lead" style="top:132px;left:112px;width:976px;text-align:center">Lorem ipsum dolor sit amet, consectetur adipiscing elit, sed do eiusmod tempor incididunt ut labore et dolore magna aliqua. Ut enim ad minim veniam, quis nostrud exercitation ullamco laboris nisi ut aliquip ex ea commodo consequat. Duis aute irure dolor in reprehenderit in voluptate velit esse cillum dolore eu fugiat nulla pariatur. Lorem ipsum dolor sit amet, consectetur adipiscing elit, sed do eiusmod tempor incididunt ut labore et dolore magna aliqua. Lorem ipsum dolor sit amet, consectetur adipiscing elit, sed do eiusmod tempor incididunt ut labore et dolore magna aliqua.</p>

  <svg class="abs" style="top:320px;left:600px" width="260" height="310" viewBox="0 0 260 310">
    <line x1="45" y1="10" x2="71" y2="48" stroke="#111" stroke-width="1.5"/>
    <line x1="213" y1="10" x2="187" y2="48" stroke="#111" stroke-width="1.5"/>
    <line x1="130" y1="240" x2="130" y2="290" stroke="#111" stroke-width="1.5"/>
  </svg>
  <div class="tag" style="top:290px;left:598px">ipsum</div>
  <div class="tag" style="top:290px;left:777px">ipsum</div>
  <div class="tag" style="top:610px;left:687px">ipsum</div>

  <div class="counter" style="top:370px;left:116px;--c:var(--blue)">DAY<br><span class="num">03</span></div>
  <div class="counter" style="top:370px;left:378px;--c:var(--deep)">HOURS<br><span class="num">10</span></div>
  <div class="counter" style="top:370px;left:640px;--c:var(--cyan);box-shadow:0 6px 18px rgba(0,0,0,.35)">MINUTES<br><span class="num">08</span></div>
  <div class="counter" style="top:370px;left:903px;--c:var(--navy)">SECONDS<br><span class="num">06</span></div>
</section>

<section class="platforms">
  <div role="img" aria-label="Faint background photo of a business handshake" class="abs" style="top:0;left:0;width:1200px;height:632px;background:radial-gradient(ellipse at 80% 20%,rgba(255,255,255,.5),rgba(255,255,255,0) 60%)"></div>
  <h2 class="abs center underline" style="top:70px">OUR INVESTMENT PLATFORMS</h2>
  <p class="abs lead center" style="top:120px">Lorem ipsum dolor sit amet, consectetur adipiscing elit, sed do eiusmod tempor incididunt ut labore et dolore magna aliqua.<br>Ut enim ad minim veniam, quis nostrud exercitation ullamco</p>
</section>
<div class="card" style="left:78px"><div class="photo" role="img" aria-label="Photo of a man working at a laptop"></div><h3>Lorem ipsum</h3><p>Lorem ipsum dolor sit<br>incididunt et dolore magna</p><div class="more">Read More »</div></div>
<div class="card" style="left:289px"><div class="photo" role="img" aria-label="Photo of two colleagues reviewing a laptop"></div><h3>Lorem ipsum</h3><p>Lorem ipsum dolor sit<br>incididunt et dolore magna</p><div class="more">Read More »</div></div>
<div class="card featured" style="left:500px"><div class="photo" role="img" aria-label="Photo of a small model house on stacks of coins" style="background:linear-gradient(160deg,#2a2a2a,#4a3a30 60%,#7a2a22)"></div><h3>Lorem ipsum</h3><p>Lorem ipsum dolor sit<br>incididunt et dolore magna</p><div class="more">Read More »</div></div>
<div class="card" style="left:710px"><div class="photo" role="img" aria-label="Photo of hands with a pen beside a model house" style="background:linear-gradient(135deg,#c7ccd2,#d8a066 60%,#8a9cb0)"></div><h3>Lorem ipsum</h3><p>Lorem ipsum dolor sit<br>incididunt et dolore magna</p><div class="more">Read More »</div></div>
<div class="card" style="left:921px"><div class="photo" role="img" aria-label="Photo of colleagues talking in an office"></div><h3>Lorem ipsum</h3><p>Lorem ipsum dolor sit<br>incididunt et dolore magna</p><div class="more">Read More »</div></div>

<section class="edge" style="top:2047px;height:557px">
  <div class="round-photo" role="img" aria-label="Photo of a terracotta apartment building against a blue sky" style="top:88px;left:108px;background:linear-gradient(135deg,#c98b4e,#d9a56a 60%,#9aa37a)"></div>
  <h2 class="abs underline left" style="top:100px;left:565px">OUR EDGE</h2>
  <p class="abs body-copy" style="top:156px;left:565px;width:524px">Lorem ipsum dolor sit amet, consectetur adipiscing elit, sed do eiusmod tempor incididunt ut labore et dolore magna aliqua. Ut enim ad minim veniam, quis nostrud exercitation ullamco laboris nisi ut aliquip ex ea commodo consequat. Duis aute irure dolor in reprehenderit in voluptate velit esse cillum dolore eu fugiat nulla pariatur. Lorem ipsum dolor sit amet, consectetur adipiscing elit, sed do eiusmod tempor incididunt ut labore et dolore magna aliqua. Lorem ipsum dolor sit amet, consectetur adipiscing elit, sed do eiusmod tempor incididunt ut labore et dolore magna aliqua.</p>
  <div class="btn" style="top:408px;left:565px;width:257px;height:44px">Investor Information</div>
</section>

<section class="stay">
  <h2 class="abs center underline" style="top:55px;color:var(--white)">STAY UPDATED</h2>
  <p class="abs lead center" style="top:107px">Lorem ipsum dolor sit amet, consectetur adipiscing elit, sed do eiusmod tempor incididunt ut labore et dolore magna aliqua.<br>Ut enim ad minim veniam, quis nostrud exercitation ullamco</p>
</section>
<div class="field" style="left:334px;width:342px;background:var(--white);color:#111;padding-left:14px">EMAIL</div>
<div class="field" style="left:703px;width:161px;background:var(--black);color:var(--white);justify-content:center">SUBMIT</div>

<section class="responsibility" style="top:2908px;height:557px">
  <h2 class="abs underline left" style="top:95px;left:110px">OUR RESPONSIBILITY</h2>
  <p class="abs body-copy" style="top:152px;left:110px;width:524px">Lorem ipsum dolor sit amet, consectetur adipiscing elit, sed do eiusmod tempor incididunt ut labore et dolore magna aliqua. Ut enim ad minim veniam, quis nostrud exercitation ullamco laboris nisi ut aliquip ex ea commodo consequat. Duis aute irure dolor in reprehenderit in voluptate velit esse cillum dolore eu fugiat nulla pariatur. Lorem ipsum dolor sit amet, consectetur adipiscing elit, sed do eiusmod tempor incididunt ut labore et dolore magna aliqua. Lorem ipsum dolor sit amet, consectetur adipiscing elit, sed do eiusmod tempor incididunt ut labore et dolore magna aliqua.</p>
  <div class="btn" style="top:404px;left:110px;width:154px;height:45px">Read More</div>
  <div class="round-photo" role="img" aria-label="Photo of business colleagues meeting at a desk" style="top:85px;left:710px;background:linear-gradient(135deg,#d8dde2,#6b5a50 55%,#2d3036)"></div>
</section>

<section class="touch">
  <div role="img" aria-label="Faint background photo of a smiling woman" class="abs" style="top:0;left:350px;width:500px;height:698px;background:radial-gradient(ellipse at 50% 50%,rgba(180,190,200,.25),rgba(255,255,255,0) 65%)"></div>
  <h2 class="abs center underline" style="top:70px">GET IN TOUCH</h2>
  <p class="abs lead center" style="top:121px">Lorem ipsum dolor sit amet, consectetur adipiscing elit, sed do eiusmod tempor incididunt ut labore et dolore magna aliqua.<br>Ut enim ad minim veniam, quis nostrud exercitation ullamco</p>

  <div class="abs info" style="top:208px;left:190px">
    <span class="ico"><svg width="14" height="18" viewBox="0 0 14 18"><path d="M7 0a7 7 0 0 0-7 7c0 5 7 11 7 11s7-6 7-11a7 7 0 0 0-7-7z" fill="#fff"/><circle cx="7" cy="7" r="2.5" fill="#1ea5e6"/></svg></span>
    <span>2003 Lorem ipsum dolor sit amet,<br>consectetur tempor</span>
  </div>
  <div class="abs" style="top:202px;left:493px;width:1px;height:38px;background:#555"></div>
  <div class="abs info" style="top:214px;left:552px">
    <span class="ico"><svg width="16" height="12" viewBox="0 0 16 12"><rect x="1" y="1" width="14" height="10" fill="none" stroke="#fff" stroke-width="1.6"/><path d="M1 1l7 6 7-6" fill="none" stroke="#fff" stroke-width="1.6"/></svg></span>
    <span>info@altavera-re.com</span>
  </div>
  <div class="abs" style="top:202px;left:792px;width:1px;height:38px;background:#555"></div>
  <div class="abs info" style="top:214px;left:860px">
    <span class="ico"><svg width="14" height="14" viewBox="0 0 14 14"><path d="M3 0l3 3-2 2c1 2 3 4 5 5l2-2 3 3-2 3C6 14 0 8 0 3z" fill="#fff"/></svg></span>
    <span>+1 888 888 8888</span>
  </div>

  <div class="form-field" style="top:312px;left:195px;width:394px"><label>Name</label><span>| Frist name</span></div>
  <div class="form-field" style="top:312px;left:648px;width:392px"><label>Email Address</label><span>@anymail.com</span></div>
  <div class="form-field" style="top:398px;left:195px;width:394px"><label>Phone</label><span>+1 888 888 8888</span></div>
  <div class="form-field" style="top:398px;left:650px;width:394px"><label>Subject</label><span>Lorem ipsum</span></div>
  <div class="form-field" style="top:490px;left:195px;width:867px;padding-bottom:18px"><label>Message</label><span>Lorem ipsum dolor</span></div>
  <div class="btn" style="top:586px;left:524px;width:152px;height:44px">Submit</div>
</section>

<footer class="footer">
  <h4 class="abs" style="top:66px;left:113px">IMPORTANT LINKS</h4>
  <ul class="abs links" style="top:102px;left:113px">
    <li>Home</li><li>About Us</li><li>Our Businesses</li><li>Investors Lobby</li><li>News</li><li>Contact Us</li>
  </ul>
  <div class="abs" style="top:60px;left:345px;width:1px;height:180px;background:#444"></div>
  <div class="abs brand" style="top:78px;left:420px;font-size:18px"><span class="dot" style="width:20px;height:20px"></span>ALTAVERA REAL ESTATE</div>
  <p class="abs" style="top:115px;left:382px;width:380px;text-align:center;font-size:14.5px;line-height:25px">Lorem ipsum dolor sit amet, consectetur adipiscing elit, sed do eiusmod tempor incididunt ut labore et dolore magna aliqua. Ut enim ad minim veniam, quis nostrud exercitation ullamco laboris nisi ut aliquip ex ea commodo consequat.</p>
  <div class="abs" style="top:60px;left:783px;width:1px;height:180px;background:#444"></div>
  <h4 class="abs" style="top:66px;left:850px">CONTACT DETAILS</h4>
  <div class="abs foot-info" style="top:112px;left:850px"><span class="ico" style="width:24px;height:24px"><svg width="10" height="14" viewBox="0 0 14 18"><path d="M7 0a7 7 0 0 0-7 7c0 5 7 11 7 11s7-6 7-11a7 7 0 0 0-7-7z" fill="#fff"/></svg></span><span>2003 Lorem ipsum dolor sit<br>amet, consectetur tempor</span></div>
  <div class="abs foot-info" style="top:167px;left:850px;align-items:center"><span class="ico" style="width:24px;height:24px"><svg width="12" height="9" viewBox="0 0 16 12"><rect x="1" y="1" width="14" height="10" fill="none" stroke="#fff" stroke-width="2"/><path d="M1 1l7 6 7-6" fill="none" stroke="#fff" stroke-width="2"/></svg></span><span>info@altavera-re.com</span></div>
  <div class="abs foot-info" style="top:212px;left:850px;align-items:center"><span class="ico" style="width:24px;height:24px"><svg width="11" height="11" viewBox="0 0 14 14"><path d="M3 0l3 3-2 2c1 2 3 4 5 5l2-2 3 3-2 3C6 14 0 8 0 3z" fill="#fff"/></svg></span><span>+1 888 888 8888</span></div>
  <div class="abs social" style="top:256px;left:852px"><span></span><span></span><span></span><span></span></div>
  <div class="abs" style="top:300px;left:110px;width:980px;height:1px;background:#444"></div>
  <p class="abs" style="top:318px;left:110px;font-size:14.5px">©Copyrights 2022 Altavera | All Rights Reserved</p>
  <p class="abs" style="top:356px;left:113px;font-size:14.5px;word-spacing:2px">Terms &nbsp;&nbsp;| &nbsp;&nbsp;condtions &nbsp;&nbsp;| &nbsp;&nbsp;Privacy Policy</p>
</footer>

</body>
</html>
```